Budget Brand Responsive Website

Flat vector style website needed for value based IT support company. looking for clean, illustration intensive based design. Current test site can be found at www.bright-mend.co.uk and holding page it www.brightmend.co.uk this will show text and services, please feel free to use placeholder text if you think we need alternative text in places. Emphasis should be on low cost support and services listed on the site, would be nice to see costs in bold images. important colors are the blue, orange and white, see holding page and attached image of an advert

It Company

```html
<!DOCTYPE html>
<html lang="en">
<head>
<meta charset="utf-8">
<title>Bright Mend – IT Services</title>
<link href="https://fonts.googleapis.com/css2?family=Open+Sans:wght@400;600;700;800&display=swap" rel="stylesheet">
<style>
:root{
  --blue:#2c4d8f;
  --blue-dark:#1f3a70;
  --blue-deep:#16294f;
  --orange:#e8731e;
  --grey-band:#ececec;
  --text:#555b66;
  --text-light:#8a9099;
  --white:#ffffff;
  --line:#d9dde3;
}
*{margin:0;padding:0;box-sizing:border-box}
html,body{width:1200px;height:2192px;overflow:hidden}
body{font-family:"Open Sans",Arial,sans-serif;color:var(--text);background:var(--white);font-size:13px;line-height:1.55}
.wrap{width:1040px;margin:0 auto;position:relative}

/* header */
.site-header{height:72px;background:var(--white);border-bottom:1px solid var(--line)}
.site-header .wrap{display:flex;align-items:center;height:72px}
.brand{display:flex;align-items:center;gap:10px;font-weight:800;font-size:26px;color:var(--blue);letter-spacing:.5px}
.brand-dot{width:14px;height:14px;background:var(--orange)}
.main-nav{display:flex;gap:30px;margin-left:auto;margin-right:40px}
.main-nav a{font-size:12px;font-weight:700;color:var(--blue);text-decoration:none;padding:25px 2px;letter-spacing:.5px}
.main-nav a.active{color:var(--orange);border-bottom:3px solid var(--orange)}
.header-phone{font-weight:700;font-size:16px;color:var(--orange)}

/* hero */
.hero{height:480px;position:relative;background:radial-gradient(ellipse at 70% 55%,#5d86c4 0%,#2f548f 35%,#17294a 75%,#0f1b33 100%);overflow:hidden}
.hero-photo{position:absolute;inset:0}
.hero-text{position:absolute;top:150px;left:0;right:0;text-align:center;color:var(--white)}
.hero-text h1{font-size:42px;font-weight:800;letter-spacing:1px}
.hero-text p{font-size:12px;letter-spacing:2px;font-weight:600;opacity:.9;margin-top:4px}
.hero-arrow{position:absolute;top:290px;width:36px;height:36px;border-radius:50%;background:rgba(255,255,255,.85);display:flex;align-items:center;justify-content:center}
.hero-arrow.prev{left:36px}.hero-arrow.next{right:36px}
.hero-dots{position:absolute;bottom:30px;left:0;right:0;display:flex;justify-content:center;gap:8px}
.hero-dots span{width:9px;height:9px;border-radius:50%;background:rgba(255,255,255,.5)}
.hero-dots span.on{background:var(--white)}

/* services */
.services{padding:44px 0 40px;text-align:center}
.section-title{font-size:26px;font-weight:800;color:var(--blue);letter-spacing:.5px}
.title-rule{width:300px;height:2px;background:var(--orange);margin:6px auto 18px}
.intro{max-width:960px;margin:0 auto;font-size:12px;color:var(--text)}
.service-grid{display:grid;grid-template-columns:repeat(3,1fr);gap:42px 40px;margin-top:38px;text-align:left;padding:0 60px}
.service{display:flex;gap:18px}
.service svg{flex:0 0 48px}
.service h3{font-size:13px;font-weight:800;color:var(--blue);margin-bottom:4px}
.service p{font-size:11px;line-height:1.5}

/* pricing */
.pricing{background:var(--grey-band);padding:0 0 60px;margin-top:18px;position:relative}
.pricing-tab{width:360px;height:50px;background:var(--orange);color:var(--white);font-weight:800;font-size:24px;text-align:center;line-height:50px;margin:0 auto;position:relative;top:-14px;letter-spacing:.5px}
.pricing .intro{margin-top:4px}
.price-cards{display:grid;grid-template-columns:repeat(4,1fr);gap:18px;margin-top:40px;padding:0 50px}
.price-card{background:var(--white);border:1px solid var(--line);text-align:center;padding-bottom:22px}
.price-head{background:var(--blue);color:var(--white);padding:18px 10px 16px;height:96px}
.price-head h3{font-size:24px;font-weight:800;letter-spacing:.5px}
.price-head p{font-size:10px;font-weight:700;line-height:1.35}
.price-rows{list-style:none;padding:10px 20px 8px}
.price-rows li{font-size:11px;padding:10px 0;border-bottom:1px solid var(--line)}
.btn{display:inline-block;background:var(--orange);color:var(--white);font-size:10px;font-weight:700;padding:6px 18px;letter-spacing:.5px;margin-top:14px}

/* support & expectations */
.feature-row{display:grid;grid-template-columns:1fr 1fr;gap:60px;padding:54px 0 40px}
.feature h2{font-size:22px;font-weight:800;color:var(--blue);margin-bottom:14px}
.feature-photos{display:flex;gap:14px;height:146px}
.photo{flex:1;background:linear-gradient(135deg,#c8d6e8,#6a88b8 60%,#2e4c82)}
.photo.warm{background:linear-gradient(135deg,#e7dfd4,#9aa8bd 55%,#3e5685)}
.feature-split{display:flex;gap:16px;height:146px}
.feature-split .photo{flex:0 0 250px}
.feature-split p{font-size:11px}
.feature > p{font-size:11px;margin-top:14px}

/* footer */
.site-footer{background:var(--blue);color:#d6deec;height:360px;margin-top:0;padding-top:36px}
.footer-cols{display:grid;grid-template-columns:1.4fr 1fr 1.3fr 1.2fr;gap:40px}
.site-footer h4{color:var(--white);font-size:13px;font-weight:800;margin-bottom:12px}
.site-footer p,.site-footer li{font-size:11px;line-height:1.75}
.site-footer ul{list-style:none}
.socials{display:flex;gap:8px;margin-top:14px}
.socials span{width:26px;height:26px;border-radius:50%;border:1.5px solid #d6deec}
.contact-line{display:flex;align-items:center;gap:8px}
.form-field{height:26px;background:var(--blue-dark);border:1px solid #4a68a3;margin-bottom:8px;font-size:10px;padding:4px 8px;color:#a9b8d3}
.form-field.tall{height:54px}
.btn-right{text-align:right}
.btn-right .btn{margin-top:2px}
.footer-bar{background:var(--blue-deep);height:32px;position:absolute;left:0;right:0;top:2160px}
.footer-bar .wrap{display:flex;justify-content:space-between;align-items:center;height:32px;font-size:10px;color:#b9c6dc}
.footer-bar nav{display:flex;gap:18px;font-weight:700}
</style>
</head>
<body>

<header class="site-header">
  <div class="wrap">
    <div class="brand"><span class="brand-dot"></span>BRIGHT MEND</div>
    <nav class="main-nav">
      <a class="active">HOME</a><a>SUPPORT</a><a>SERVICES</a><a>ABOUT</a><a>CONTACT</a>
    </nav>
    <div class="header-phone">☎ 01632 960 415</div>
  </div>
</header>

<section class="hero">
  <div class="hero-photo" role="img" aria-label="Photo of a hand touching a glowing digital network interface in deep blue light"></div>
  <div class="hero-text">
    <h1>IT SERVICES THE BRIGHT WAY</h1>
    <p>WE HELP OUR CLIENTS GET MORE FROM THEIR TECHNOLOGY EVERY DAY</p>
  </div>
  <div class="hero-arrow prev"><svg width="12" height="14" viewBox="0 0 12 14"><path d="M9 1 3 7l6 6" fill="none" stroke="#2c4d8f" stroke-width="2.4"/></svg></div>
  <div class="hero-arrow next"><svg width="12" height="14" viewBox="0 0 12 14"><path d="M3 1l6 6-6 6" fill="none" stroke="#2c4d8f" stroke-width="2.4"/></svg></div>
  <div class="hero-dots"><span></span><span class="on"></span><span></span></div>
</section>

<section class="services">
  <div class="wrap">
    <h2 class="section-title">SERVICES TAILORED FOR YOU</h2>
    <div class="title-rule"></div>
    <p class="intro">Lorem ipsum dolor sit amet, consectetur adipiscing elit, sed do eiusmod tempor incididunt ut labore et dolore magna aliqua. Ut enim ad minim veniam, quis nostrud exercitation ullamco laboris nisi ut aliquip ex ea commodo consequat duis aute irure dolor in reprehenderit.</p>
    <div class="service-grid">
      <div class="service">
        <svg width="48" height="48" viewBox="0 0 48 48"><path d="M10 28v-6a14 14 0 0 1 28 0v6" fill="none" stroke="#e8731e" stroke-width="4"/><rect x="6" y="26" width="9" height="13" rx="2" fill="#e8731e"/><rect x="33" y="26" width="9" height="13" rx="2" fill="#e8731e"/></svg>
        <div><h3>SUPPORT</h3><p>Lorem ipsum dolor sit amet, consectetur adipiscing elit sed do eiusmod tempor ut labore magna.</p></div>
      </div>
      <div class="service">
        <svg width="48" height="48" viewBox="0 0 48 48"><path d="M14 6l6 8-4 5c2 5 6 9 11 11l5-4 8 6-4 7C22 39 9 26 7 12z" fill="#e8731e"/></svg>
        <div><h3>VOICE</h3><p>Lorem ipsum dolor sit amet, consectetur adipiscing elit sed do eiusmod tempor ut labore magna.</p></div>
      </div>
      <div class="service">
        <svg width="48" height="48" viewBox="0 0 48 48"><circle cx="24" cy="24" r="17" fill="none" stroke="#e8731e" stroke-width="4"/><ellipse cx="24" cy="24" rx="7" ry="17" fill="none" stroke="#e8731e" stroke-width="3"/><path d="M7 24h34" stroke="#e8731e" stroke-width="3"/></svg>
        <div><h3>INTERNET</h3><p>Lorem ipsum dolor sit amet, consectetur adipiscing elit sed do eiusmod tempor ut labore magna.</p></div>
      </div>
      <div class="service">
        <svg width="48" height="48" viewBox="0 0 48 48"><path d="M24 4l16 6v12c0 11-7 18-16 22C15 40 8 33 8 22V10z" fill="#e8731e"/><path d="M17 24l5 5 9-10" fill="none" stroke="#fff" stroke-width="3.5"/></svg>
        <div><h3>SECURITY</h3><p>Lorem ipsum dolor sit amet, consectetur adipiscing elit sed do eiusmod tempor ut labore magna.</p></div>
      </div>
      <div class="service">
        <svg width="48" height="48" viewBox="0 0 48 48"><rect x="8" y="8" width="32" height="10" rx="2" fill="#e8731e"/><rect x="8" y="20" width="32" height="10" rx="2" fill="#e8731e"/><rect x="8" y="32" width="32" height="10" rx="2" fill="#e8731e"/><circle cx="34" cy="13" r="2" fill="#fff"/><circle cx="34" cy="25" r="2" fill="#fff"/><circle cx="34" cy="37" r="2" fill="#fff"/></svg>
        <div><h3>HOSTING</h3><p>Lorem ipsum dolor sit amet, consectetur adipiscing elit sed do eiusmod tempor ut labore magna.</p></div>
      </div>
      <div class="service">
        <svg width="48" height="48" viewBox="0 0 48 48"><path d="M14 36a9 9 0 0 1-1-18 11 11 0 0 1 21-2 9 9 0 0 1 2 20z" fill="#e8731e"/></svg>
        <div><h3>CLOUD</h3><p>Lorem ipsum dolor sit amet, consectetur adipiscing elit sed do eiusmod tempor ut labore magna.</p></div>
      </div>
    </div>
  </div>
</section>

<section class="pricing">
  <div class="pricing-tab">PRICING COST</div>
  <div class="wrap">
    <p class="intro">Lorem ipsum dolor sit amet, consectetur adipiscing elit, sed do eiusmod tempor incididunt ut labore et dolore magna aliqua. Ut enim ad minim veniam, quis nostrud exercitation ullamco laboris nisi ut aliquip ex ea commodo consequat duis aute irure dolor in reprehenderit.</p>
    <div class="price-cards">
      <div class="price-card">
        <div class="price-head"><h3>SUPPORT</h3><p>UNLIMITED REMOTE<br>DESKTOP SUPPORT</p></div>
        <ul class="price-rows"><li>Remote help desk</li><li>On-site visits included</li><li>Server monitoring</li></ul>
        <span class="btn">SIGN UP</span>
      </div>
      <div class="price-card">
        <div class="price-head"><h3>VOICE</h3><p>CONNECTED FREE<br>CALL CHARGES</p></div>
        <ul class="price-rows"><li>Free line rental</li><li>Low rates from 1.5p</li><li>Flexible number plans</li></ul>
        <span class="btn">SIGN UP</span>
      </div>
      <div class="price-card">
        <div class="price-head"><h3>HOSTING</h3><p>STORES AND ONLINE</p></div>
        <ul class="price-rows"><li>Email hosting from £3</li><li>Website hosting plans</li><li>Offsite daily backups</li></ul>
        <span class="btn">SIGN UP</span>
      </div>
      <div class="price-card">
        <div class="price-head"><h3>CLOUD</h3><p>REDUCE COSTS &amp; INCREASE<br>PERFORMANCE</p></div>
        <ul class="price-rows"><li>Online backup</li><li>Hosted applications</li><li>Virtual desktops</li></ul>
        <span class="btn">SIGN UP</span>
      </div>
    </div>
  </div>
</section>

<section class="wrap feature-row">
  <div class="feature">
    <h2>TECHNICAL SUPPORT</h2>
    <div class="feature-photos">
      <div class="photo warm" role="img" aria-label="Photo of a support agent wearing a headset"></div>
      <div class="photo" role="img" aria-label="Photo of a technician working on network hardware"></div>
    </div>
    <p>Lorem ipsum dolor sit amet, consectetur adipiscing elit, sed do eiusmod tempor incididunt ut labore et dolore magna aliqua. Ut enim ad minim veniam quis nostrud exercitation.</p>
    <span class="btn">READ MORE</span>
  </div>
  <div class="feature">
    <h2>WE EXCEED EXPECTATIONS</h2>
    <div class="feature-split">
      <div class="photo warm" role="img" aria-label="Photo of a business team smiling at a meeting"></div>
      <p>Lorem ipsum dolor sit amet, consectetur adipiscing elit, sed do eiusmod tempor incididunt ut labore et dolore magna aliqua ut enim ad minim veniam.</p>
    </div>
    <p>Lorem ipsum dolor sit amet, consectetur adipiscing elit, sed do eiusmod tempor incididunt ut labore et dolore magna aliqua.</p>
    <span class="btn">READ MORE</span>
  </div>
</section>

<footer class="site-footer">
  <div class="wrap footer-cols">
    <div>
      <h4>ABOUT BRIGHT MEND</h4>
      <p>Bright Mend is a value based IT support provider helping small and growing businesses across the region keep systems running smoothly at a fair monthly price.</p>
      <div class="socials"><span></span><span></span><span></span><span></span></div>
    </div>
    <div>
      <h4>SERVICES</h4>
      <ul><li>Support</li><li>Voice</li><li>Internet</li><li>Security</li><li>Hosting</li><li>Cloud</li></ul>
    </div>
    <div>
      <h4>CONTACT US</h4>
      <p class="contact-line"><svg width="12" height="14" viewBox="0 0 12 14"><path d="M6 0a5 5 0 0 0-5 5c0 4 5 9 5 9s5-5 5-9a5 5 0 0 0-5-5z" fill="#e8731e"/></svg>Unit 4, Harbour Yard, Example Road</p>
      <p class="contact-line"><svg width="12" height="14" viewBox="0 0 12 14"><path d="M6 0a5 5 0 0 0-5 5c0 4 5 9 5 9s5-5 5-9a5 5 0 0 0-5-5z" fill="#e8731e"/></svg>Northfield, ZZ1 4AB</p>
      <p class="contact-line"><svg width="12" height="12" viewBox="0 0 12 12"><path d="M3 1l2 3-1 1.5c.8 1.4 1.8 2.4 3 3L8.5 7l3 2-1.5 2.5C5 11 1 7 .8 2z" fill="#e8731e"/></svg>Tel: 01632 960 415</p>
      <p class="contact-line"><svg width="12" height="10" viewBox="0 0 12 10"><rect width="12" height="10" fill="#e8731e"/><path d="M0 0l6 5 6-5" fill="none" stroke="#2c4d8f" stroke-width="1.2"/></svg>hello@brightmend.co.uk</p>
    </div>
    <div>
      <h4>CONTACT FORM</h4>
      <div class="form-field">Your Name</div>
      <div class="form-field">Your Email</div>
      <div class="form-field tall">Your Message</div>
      <div class="btn-right"><span class="btn">SUBMIT</span></div>
    </div>
  </div>
</footer>
<div class="footer-bar">
  <div class="wrap">
    <nav><span>HOME</span><span>SUPPORT</span><span>SERVICES</span><span>ABOUT</span><span>CONTACT</span></nav>
    <span>Copyright © 2015 · All Rights Reserved</span>
  </div>
</div>

</body>
</html>
```